Premium Organic Ceremonial Matcha Green Tea - Product Label

Two Label Bag Sizes: 18x30cm and 17x24cm

Be EXTRA Creative.. please message me with any questions and I will respond quickly.

Target Market(s)

Health, Organic, Green Tea Matcha Drinkers

Industry/Entity Type

Product

Requirements
Must have
• Organic Matcha Green Tea
• Try to incorporate geometry in logo into design... not mandatory but preferred for branding.

```html
<!DOCTYPE html>
<html lang="en">
<head>
<meta charset="utf-8">
<title>Verdant Grove Organic Matcha – Label</title>
<link href="https://fonts.googleapis.com/css2?family=Poppins:wght@400;500;600&display=swap" rel="stylesheet">
<style>
  :root {
    --bg: #e9efe4;
    --leaf-dark: #1f4a12;
    --leaf-mid: #3d7a1e;
    --leaf-bright: #6fae2e;
    --sky-warm: #c9744a;
    --sky-dusk: #6b4a5c;
    --gold: #f3d21a;
    --white: #ffffff;
    --hex-fill: rgba(20, 60, 12, 0.35);
    --matcha: #6f9a2c;
    --bowl: #f2f2ee;
  }
  * { margin: 0; padding: 0; box-sizing: border-box; }
  html, body { width: 1200px; height: 921px; overflow: hidden; }
  body {
    background: var(--bg);
    font-family: "Poppins", sans-serif;
    position: relative;
  }
  .label {
    position: absolute;
    left: 381px;
    top: 128px;
    width: 438px;
    height: 640px;
    border-radius: 10px;
    overflow: hidden;
    box-shadow: 0 10px 30px rgba(0,0,0,0.18);
  }
  .label__scene {
    position: absolute; inset: 0;
    background:
      linear-gradient(180deg,
        var(--sky-dusk) 0%,
        var(--sky-warm) 10%,
        #7d5a4e 22%,
        #4e6a2e 34%,
        var(--leaf-mid) 55%,
        var(--leaf-dark) 100%);
  }
  .label__hang-slot {
    position: absolute; left: 175px; top: 26px;
    width: 88px; height: 22px; border-radius: 11px;
    background: rgba(255,255,255,0.85);
  }
  .brand {
    position: absolute; left: 0; right: 0; top: 224px;
    text-align: center;
    font-weight: 600; font-size: 26px;
    color: var(--gold);
    display: flex; justify-content: center; align-items: center; gap: 10px;
  }
  .brand__dot {
    width: 14px; height: 14px; border-radius: 50%;
    background: var(--gold);
  }
  .tagline {
    position: absolute; left: 0; right: 0; top: 262px;
    text-align: center;
    font-weight: 600; font-size: 16px;
    color: var(--gold);
  }
  .seal {
    position: absolute; left: 330px; top: 142px;
    width: 66px; height: 66px; border-radius: 50%;
    background: var(--white);
    border: 4px solid var(--leaf-mid);
  }
  .benefits { position: absolute; left: 0; top: 0; }
  .benefits text {
    font-family: "Poppins", sans-serif;
    fill: var(--white);
    font-size: 9.5px;
    text-anchor: middle;
  }
  .benefits .core-text {
    fill: var(--leaf-mid); font-size: 13px; font-weight: 500;
  }
  .uses {
    position: absolute; left: 52px; top: 510px;
    display: flex; gap: 14px;
  }
  .use { display: flex; flex-direction: column; align-items: center; gap: 4px; width: 44px; }
  .use__icon {
    width: 38px; height: 38px; border-radius: 50%;
    border: 2px solid var(--white);
    background: rgba(255,255,255,0.12);
    display: flex; align-items: center; justify-content: center;
  }
  .use__name { font-size: 9px; color: var(--white); }
  .net-weight {
    position: absolute; left: 56px; top: 584px;
    font-size: 9px; color: var(--white);
  }
  .powder-bowl {
    position: absolute; left: 262px; top: 492px;
    width: 150px; height: 130px; border-radius: 50%;
    background: radial-gradient(circle at 50% 45%, var(--matcha) 0 48%, var(--bowl) 50% 60%, transparent 62%);
  }
</style>
</head>
<body>
  <section class="label" aria-label="Matcha pouch front label">
    <div class="label__scene" role="img" aria-label="Photo of tea plantation hills at sunrise fading into close-up green tea leaves"></div>
    <div class="label__hang-slot"></div>

    <div class="seal" role="img" aria-label="Organic certification seal"></div>

    <div class="brand"><span class="brand__dot"></span>Verdant Grove</div>
    <div class="tagline">100% Pure Organic Matcha</div>

    <svg class="benefits" width="438" height="640" viewBox="0 0 438 640" aria-label="Matcha benefits">
      <defs>
        <polygon id="hex" points="36,0 18,31.2 -18,31.2 -36,0 -18,-31.2 18,-31.2"/>
      </defs>
      <g fill="var(--hex-fill)" stroke="var(--white)" stroke-width="2.5" stroke-linejoin="round">
        <use href="#hex" x="216" y="333.6"/>
        <use href="#hex" x="162" y="364.8"/>
        <use href="#hex" x="270" y="364.8"/>
        <use href="#hex" x="162" y="427.2"/>
        <use href="#hex" x="270" y="427.2"/>
        <use href="#hex" x="216" y="458.4"/>
        <use href="#hex" x="216" y="396" fill="var(--white)"/>
      </g>
      <text x="216" y="331">Antioxidants</text>
      <text x="216" y="343">Powerhouse</text>
      <text x="162" y="362">Maximum</text>
      <text x="162" y="374">Potency</text>
      <text x="270" y="362">Fat</text>
      <text x="270" y="374">Burner</text>
      <text class="core-text" x="216" y="400.5">Matcha</text>
      <text x="162" y="424.5">Culinary</text>
      <text x="162" y="436.5">Grade</text>
      <text x="270" y="418.5">Increases</text>
      <text x="270" y="430.5">Mental</text>
      <text x="270" y="442.5">Focus</text>
      <text x="216" y="455.5">Energy</text>
      <text x="216" y="467.5">Booster</text>
    </svg>

    <div class="uses">
      <div class="use">
        <div class="use__icon">
          <svg width="18" height="20" viewBox="0 0 18 20" fill="none" stroke="#fff" stroke-width="1.6"><path d="M3 5h12l-2 14H5z"/><path d="M2 5h14M9 5l2-4"/></svg>
        </div>
        <span class="use__name">Smoothies</span>
      </div>
      <div class="use">
        <div class="use__icon">
          <svg width="20" height="20" viewBox="0 0 20 20" fill="none" stroke="#fff" stroke-width="1.6"><path d="M4 9h12l-2 9H6z"/><path d="M4 9a6 5 0 0 1 12 0"/></svg>
        </div>
        <span class="use__name">Baking</span>
      </div>
      <div class="use">
        <div class="use__icon">
          <svg width="22" height="18" viewBox="0 0 22 18" fill="none" stroke="#fff" stroke-width="1.6"><path d="M3 4h13v6a6 6 0 0 1-13 0z"/><path d="M16 6h2a2 2 0 0 1 0 4h-2"/><path d="M1 17h18"/></svg>
        </div>
        <span class="use__name">Lattes</span>
      </div>
    </div>

    <div class="net-weight">Net weight 113g / 4oz</div>

    <div class="powder-bowl" role="img" aria-label="Photo of matcha powder in a white bowl"></div>
  </section>
</body>
</html>
```